business card

Business card for new business.
Red and black corporate colors.
Card can have an Indsutrial feel to it. Feel free to add Rust, Bolted steel, or graphics as you see fit. We provide highly specialized services to the below mentioned industries.
Keep information out of corners so that if I want I can choose rounded corners.
Information
- front. name - title - phone - email
- Rear
Refining - Rail - Infrastructure - Mining - Energy
Calgary - Edmonton - Fort McMurray - Revelstoke - Vancouver

```html
<!DOCTYPE html>
<html lang="en">
<head>
<meta charset="utf-8">
<title>Ironvale Business Card</title>
<link rel="stylesheet" href="https://fonts.googleapis.com/css2?family=Lato:wght@400;700;900&display=swap">
<style>
  :root {
    --bg: #3a3a3a;
    --card-black: #050505;
    --card-white: #ffffff;
    --brand-red: #e3141d;
    --brand-grey: #8c8c8c;
    --ink: #1a1a1a;
    --ink-soft: #2b2b2b;
    --on-dark: #ffffff;
  }
  * { box-sizing: border-box; margin: 0; padding: 0; }
  html, body {
    width: 1200px; height: 1059px; overflow: hidden;
    background: var(--bg);
    font-family: "Lato", Arial, sans-serif;
  }
  .sheet {
    width: 1200px; height: 1059px;
    display: flex; flex-direction: column; align-items: center; justify-content: center;
    gap: 40px;
  }
  .card {
    position: relative;
    width: 840px; height: 480px;
    overflow: hidden;
  }
  .card::after {
    content: ""; position: absolute; left: 0; right: 0; bottom: 0;
    height: 14px; background: var(--brand-red);
  }

  /* Back */
  .card--back { background: var(--card-black); color: var(--on-dark); }
  .card--back .wordmark {
    position: absolute; top: 150px; left: 0; right: 0;
    display: flex; align-items: center; justify-content: center; gap: 18px;
  }
  .wordmark__mark { width: 22px; height: 22px; background: var(--brand-red); }
  .wordmark__name {
    font-weight: 900; font-size: 84px; letter-spacing: 1px; line-height: 1;
    color: var(--brand-grey);
  }
  .card--back .reach {
    position: absolute; top: 320px; left: 0; right: 0;
    text-align: center; font-size: 22px; line-height: 1.45;
  }
  .reach .dot { color: var(--brand-red); padding: 0 6px; }

  /* Front */
  .card--front { background: var(--card-white); color: var(--ink); }
  .card--front .wordmark {
    position: absolute; top: 190px; left: 70px; width: 330px;
    display: flex; align-items: center; gap: 12px;
  }
  .card--front .wordmark__name { font-size: 54px; }
  .card--front .wordmark__mark { width: 16px; height: 16px; }
  .divider {
    position: absolute; left: 440px; top: 110px;
    width: 2px; height: 190px; background: var(--brand-red);
  }
  .contact { position: absolute; left: 480px; top: 110px; }
  .contact__name { color: var(--brand-red); font-size: 30px; font-weight: 400; }
  .contact__title { font-size: 20px; color: var(--ink-soft); margin-top: 2px; margin-bottom: 14px; }
  .contact__list { list-style: none; }
  .contact__list li {
    display: flex; align-items: center; gap: 12px;
    font-size: 20px; line-height: 1.5; color: var(--ink);
  }
  .contact__list svg { width: 16px; height: 16px; fill: var(--brand-red); flex: none; }
  .address {
    position: absolute; right: 70px; bottom: 60px;
    font-size: 24px; color: var(--ink);
  }
</style>
</head>
<body>
<main class="sheet">
  <section class="card card--back" aria-label="Card back">
    <div class="wordmark">
      <span class="wordmark__mark"></span>
      <span class="wordmark__name">IRONVALE</span>
    </div>
    <p class="reach">
      Fabrication<span class="dot">•</span>Marine<span class="dot">•</span>Pipelines<span class="dot">•</span>Forestry<span class="dot">•</span>Power<br>
      Northgate<span class="dot">•</span>Ridgeford<span class="dot">•</span>Port Allenby<span class="dot">•</span>Stonecrest<span class="dot">•</span>Westhaven
    </p>
  </section>

  <section class="card card--front" aria-label="Card front">
    <div class="wordmark">
      <span class="wordmark__mark"></span>
      <span class="wordmark__name">IRONVALE</span>
    </div>
    <div class="divider"></div>
    <div class="contact">
      <h1 class="contact__name">Daniel Hartley</h1>
      <p class="contact__title">Manager</p>
      <ul class="contact__list">
        <li>
          <svg viewBox="0 0 16 16" aria-hidden="true"><path d="M3.5 1.5l2.5 0 1 3.5-1.6 1.2a8 8 0 0 0 4.4 4.4L11 9l3.5 1v2.5c0 .8-.7 1.5-1.5 1.5C7 14 2 9 2 3c0-.8.7-1.5 1.5-1.5z"/></svg>
          555 010 4422
        </li>
        <li>
          <svg viewBox="0 0 16 16" aria-hidden="true"><path d="M1 3h14v10H1z M2 4.2v.4l6 4 6-4v-.4z" fill-rule="evenodd"/></svg>
          info@ironvale.com
        </li>
        <li>
          <svg viewBox="0 0 16 16" aria-hidden="true"><circle cx="8" cy="8" r="7"/><path d="M1 8h14M8 1c-3 3-3 11 0 14M8 1c3 3 3 11 0 14" stroke="#fff" stroke-width="1" fill="none"/></svg>
          www.ironvale.com
        </li>
      </ul>
    </div>
    <p class="address">48 Millgate Road, Harbor City, TX 70000</p>
  </section>
</main>
</body>
</html>
```